Simple, 1-Page Project - Life-saving AED Devices

We recently kicked off a project to bring all geographic location records for automatic emergency defibrillators (AEDs) in the State of New York online (instead of kept in paper in drawers). This hope is that is will ultimately save thousands of lives, as 9-1-1 operators will be able to quickly direct civilians to the nearest AED to bring to people suffering a cardiac event (e.g., a heart attack).

This page will be used to describe this effort, our progress thus far and how far we have left to go.

I am looking for a 1-page design - coded for both a responsive version for mobile devices and a traditional version - that would ***ideally*** plug into my existing WordPress site (https://qv-lmt.org), but it's not a requirement.

Target Market(s)

General public (non-physicians/non-EMTs)

Requirements
Must have
• - Our logo (please note, our logo is the Birchfield Vale Chapter logo...attached)
Nice to have
• - Would be wonderful to have an area with a clickable map showing where the participating regions are - which, once clicked, will take to you their specific sites. Regions are large chunks of land encompassing multiple towns, NOT a singular, specific place A nice-looking Google Map, a la Plumtail Grids (https://plumtailgrids.com/) would be cool if this were possible..
• - If you need a headline or page title, you can use: "Bringing AEDs in New York Online"
• - Would be nice if the design incorporated the color scheme of our brand (see attachment) and/or our main website: https://qv-lmt.org/
• - Would be nice to have some AED imagery - I attached some common symbols seen in AED advertising for inspiration
Should not have
• - This is a serious topic, so the design should be respectful and not too silly/cartoonish
• - Stock images, if chosen, should be thoughtful and classy

```html
<!DOCTYPE html>
<html lang="en">
<head>
<meta charset="utf-8">
<title>Bringing AEDs in New York Online</title>
<link href="https://fonts.googleapis.com/css2?family=Montserrat:wght@500;600;700&family=Open+Sans:ital,wght@0,400;0,600;1,400&display=swap" rel="stylesheet">
<style>
:root{
  --navy:#1b2a5a;
  --navy-deep:#17244f;
  --gold:#a9a36a;
  --gold-btn:#b3ab72;
  --ink:#1b1b1b;
  --muted:#555a66;
  --ice:#e6f0f6;
  --footer:#1b1b1b;
  --line:#d9dde3;
}
*{box-sizing:border-box;margin:0;padding:0}
html,body{width:1200px;height:3869px;overflow:hidden}
body{font-family:"Open Sans",sans-serif;color:var(--ink);background:#fff;position:relative}
h1,h2,h3,.heading{font-family:"Montserrat",sans-serif}
.abs{position:absolute}

/* header */
.topbar{position:absolute;top:0;left:0;width:1200px;height:91px;background:#fff}
.brand{position:absolute;left:90px;top:12px;display:flex;align-items:center;gap:10px}
.brand-seal{width:68px;height:68px;border-radius:50%;background:var(--navy)}
.brand-name{font-family:"Open Sans",sans-serif;font-weight:600;color:var(--navy);font-size:19px;line-height:21px;letter-spacing:.5px}
.info{position:absolute;top:14px;display:flex;flex-direction:column}
.info .big{font-size:23px;color:var(--ink);display:flex;align-items:center;gap:8px}
.info .small{font-size:11.5px;line-height:14px;color:#333;margin-top:4px;padding-left:2px}
.divider{position:absolute;top:12px;width:1px;height:66px;background:#ddd}
.social{position:absolute;top:31px;display:flex;gap:25px;left:974px}
.social span{width:28px;height:28px;background:var(--ink);display:block;border-radius:3px}

.nav{position:absolute;top:91px;left:0;width:1200px;height:59px;background:var(--navy);display:flex;justify-content:center;gap:45px;align-items:center;padding-left:30px}
.nav a{color:#fff;text-decoration:none;font-family:"Montserrat",sans-serif;font-weight:500;font-size:16px;position:relative}
.nav a.active::after{content:"";position:absolute;left:0;right:0;bottom:-12px;height:3px;background:#fff}

/* hero */
.hero{position:absolute;top:150px;left:0;width:1200px;height:552px;background:linear-gradient(135deg,#4b5560 0%,#6b7d82 35%,#8fa6ae 55%,#3d4a4e 100%)}
.hero-shade{position:absolute;inset:0;background:rgba(20,25,35,.35)}
.hero h1{position:absolute;top:120px;left:0;width:1200px;text-align:center;color:#fff;font-size:55px;font-weight:700}
.hero p{position:absolute;top:200px;left:240px;width:720px;text-align:center;color:#fff;font-size:17px;line-height:28px}
.btn-start{position:absolute;top:279px;left:501px;width:198px;height:52px;background:var(--gold-btn);color:#fff;border:2px solid #d5d0a6;font-family:"Montserrat",sans-serif;font-size:20px;display:flex;align-items:center;justify-content:center}
.dots{position:absolute;top:507px;left:563px;display:flex;gap:15px}
.dots span{width:15px;height:15px;border:2px solid #fff;border-radius:50%;display:block;position:relative}
.dots span.on::after{content:"";position:absolute;inset:3px;background:#fff;border-radius:50%}

/* about */
.about-title{top:818px;left:89px;font-size:41px;color:var(--navy);font-weight:700}
.about-text{top:900px;left:89px;width:422px;font-size:16px;line-height:27px;color:var(--muted);text-align:justify}
.read-more{font-family:"Montserrat",sans-serif;font-weight:600;color:var(--gold);font-size:16px}
.about-photo{top:834px;left:700px;width:411px;height:245px;background:linear-gradient(160deg,#b89a78 0%,#d9d3cb 45%,#c0424a 80%,#6d5a4a 100%)}

/* services */
.services{top:1173px;left:0;width:1200px;height:550px;background:linear-gradient(90deg,#f3f7fa 0%,var(--ice) 60%,#dceaf3 100%)}
.section-title{position:absolute;left:0;width:1200px;text-align:center;color:var(--navy);font-weight:700;font-size:41px}
.section-lead{position:absolute;left:250px;width:700px;text-align:center;font-size:16px;line-height:27px;color:var(--muted)}
.card{position:absolute;top:233px;width:304px;height:263px;background:#fff;border:2px solid #dfe4ea;text-align:center;padding-top:20px}
.card.feature{background:var(--navy);border-color:var(--navy);color:#fff}
.card svg{display:block;margin:0 auto}
.card h3{font-size:22px;font-weight:700;color:var(--navy);margin-top:20px}
.card.feature h3{color:#fff}
.card p{font-size:13.5px;line-height:22px;color:#555;margin:12px 18px 0}
.card.feature p{color:#e7e9f2}
.band{top:1723px;left:0;width:1200px;height:27px;background:#f1f1f1}

/* news */
.news-feature{top:2025px;left:89px;width:492px;height:405px}
.news-feature .photo{height:310px;background:linear-gradient(150deg,#c9a78f 0%,#d7c2b4 35%,#cf3a3f 65%,#5fb3c2 100%)}
.news-feature .caption{height:95px;background:var(--navy);color:#fff;padding:16px 17px}
.news-feature h3{font-size:21px;font-weight:600}
.meta{font-size:14px;display:flex;align-items:center;gap:8px}
.meta .bar{width:1px;height:20px;background:currentColor;margin:0 4px}
.arrows{position:absolute;right:30px;bottom:22px;display:flex;gap:10px}
.arrows span{width:30px;height:30px;border-radius:50%;background:#fff;display:flex;align-items:center;justify-content:center}
.news-thumb{left:604px;width:192px;height:192px}
.news-item{left:817px;width:290px}
.news-item .meta{color:#222;font-size:14px}
.news-item h3{font-size:21px;font-weight:600;color:var(--navy);margin-top:12px}
.news-item p{font-size:14px;line-height:22px;color:var(--muted);margin-top:10px;text-align:justify}
.news-item .read-more{display:block;margin-top:10px;font-size:15px}

/* testimonials */
.testimonials{top:2532px;left:0;width:1200px;height:518px;background:radial-gradient(ellipse at 50% 55%,#223468 0%,var(--navy-deep) 70%)}
.testimonials h2{position:absolute;top:56px;left:0;width:1175px;text-align:center;color:#fff;font-size:41px;font-weight:600}
.quote-box{position:absolute;top:135px;left:150px;width:898px;height:322px;border:1px solid #55608a}
.quote-box blockquote{position:absolute;top:52px;left:70px;width:785px;color:#fff;font-style:italic;font-size:20px;line-height:33px;text-align:justify}
.qmark{position:absolute;color:#fff;font-family:Georgia,serif;font-size:56px;font-weight:700;line-height:1}
.avatar{position:absolute;top:213px;left:53px;width:62px;height:62px;border-radius:50%;background:linear-gradient(#d8b894,#a07a58)}
.who{position:absolute;top:218px;left:131px;color:#fff}
.who b{display:block;font-weight:400;font-size:19px}
.who i{font-size:14px}
.case-btn{position:absolute;top:228px;left:731px;width:130px;height:38px;border:1px solid #fff;border-radius:3px;color:#fff;font-size:13px;display:flex;align-items:center;justify-content:center}

/* map */
.map{top:3050px;left:0;width:1200px;height:421px;background:linear-gradient(120deg,#f2f2f2 0%,#e6e6e6 40%,#d8d8d8 48%,#ececec 60%,#f4f4f4 100%)}
.map-pop{position:absolute;background:#fff;border:1px solid #cfcfcf;padding:12px 16px;font-size:14px;line-height:19px;color:#333}

/* footer */
.footer{top:3471px;left:0;width:1200px;height:398px;background:var(--footer);color:#fff}
.footer .brand{left:92px;top:75px}
.footer .brand-seal{width:60px;height:60px;background:#fff}
.footer .brand-name{color:#fff;font-size:17px;line-height:19px}
.footer h4{position:absolute;top:105px;font-family:"Open Sans",sans-serif;font-weight:600;font-size:23px}
.footer ul{position:absolute;list-style:none;font-size:16px;line-height:27px}
.contact-row{position:absolute;left:851px;display:flex;gap:18px;font-size:17px;line-height:33px}
.copyright{position:absolute;top:359px;left:0;width:1200px;text-align:center;font-size:17px}
</style>
</head>
<body>

<header class="topbar">
  <div class="brand">
    <div class="brand-seal"></div>
    <div class="brand-name">BIRCHFIELD VALE<br>HEART<br>SOCIETY</div>
  </div>
  <div class="info" style="left:524px">
    <div class="big"><svg width="18" height="18" viewBox="0 0 20 20"><circle cx="10" cy="10" r="8.5" fill="none" stroke="#1b2a5a" stroke-width="1.8"/><path d="M10 5v5l3 2" fill="none" stroke="#1b2a5a" stroke-width="1.8"/></svg>8.00-19.00</div>
    <div class="small">Our Opening hours<br>Mon-fri</div>
  </div>
  <div class="divider" style="left:684px"></div>
  <div class="info" style="left:708px">
    <div class="big"><svg width="18" height="18" viewBox="0 0 24 24"><path fill="#1b2a5a" d="M6.6 10.8a15 15 0 0 0 6.6 6.6l2.2-2.2c.3-.3.7-.4 1-.2 1.1.4 2.3.6 3.6.6.6 0 1 .4 1 1V20c0 .6-.4 1-1 1A17 17 0 0 1 3 4c0-.6.4-1 1-1h3.5c.6 0 1 .4 1 1 0 1.3.2 2.5.6 3.6.1.3 0 .7-.2 1z"/></svg>(555) 014-0228</div>
    <div class="small">Contact Us Now For A<br>Aed Devices.</div>
  </div>
  <div class="divider" style="left:930px"></div>
  <div class="social" aria-label="Social links"><span></span><span></span><span></span></div>
</header>

<nav class="nav">
  <a class="active">HOME</a><a>ABOUT US</a><a>SERVICES &amp; PRODUCTS</a><a>RESOURCES</a><a>BLOG</a><a>CONTACT US</a>
</nav>

<section class="hero">
  <div role="img" aria-label="Photo of AED pads being placed on a patient's chest during a rescue" class="hero-shade"></div>
  <h1>Bringing AEDs in New York Online</h1>
  <p>Lorem ipsum dolor sit amet, consectetur adipiscing elit. Donec sapien sapien, molestie ac convallis vitae, gravida ut ex.&nbsp; In non sem a velit mollis elementum.</p>
  <div class="btn-start">GET STARTED</div>
  <div class="dots"><span></span><span class="on"></span><span></span></div>
</section>

<h2 class="abs about-title">About Us</h2>
<p class="abs about-text">Lorem ipsum dolor sit amet, consectetur adipiscing elit. Donec sapien sapien, molestie ac convallis vitae, gravida ut ex. In non sem a velit mollis elementum. Praesent porta urna in maximus dapibus. Aliquam velit mi, consectetur ullamcorper quam sit amet.</p>
<div class="abs read-more" style="top:1075px;left:88px">Read More</div>
<div class="abs about-photo" role="img" aria-label="Photo of a CPR training manikin with an AED trainer and red AED case"></div>

<section class="abs services">
  <h2 class="section-title" style="top:52px">Services</h2>
  <p class="section-lead" style="top:114px">Lorem ipsum dolor sit amet, consectetur adipiscing elit. Donec sapien sapien, molestie ac convallis vitae.</p>
  <div class="card" style="left:117px">
    <svg width="76" height="92" viewBox="0 0 76 92" fill="none" stroke="#1b1b1b" stroke-width="3"><rect x="4" y="30" width="68" height="58" rx="3"/><rect x="22" y="4" width="34" height="40" rx="2"/><path d="M28 14h22M28 22h22M28 30h14M12 58h52M12 68h52M12 78h30"/><rect x="50" y="74" width="14" height="8"/></svg>
    <h3>Lorem ipsum dolor</h3>
    <p>Praesent porta urna in maximus dapibus. Aliquam velit mi, consectetur ullamcorper quam sit amet, imperdiet</p>
  </div>
  <div class="card feature" style="left:451px">
    <svg width="76" height="92" viewBox="0 0 76 92" fill="none" stroke="#fff" stroke-width="3"><rect x="4" y="4" width="68" height="52" rx="6"/><rect x="12" y="12" width="40" height="22" rx="2"/><path d="M14 24h8l4-7 5 13 4-8h13"/><circle cx="62" cy="20" r="5"/><path d="M14 56v30h16V56M46 56v30h16V56M20 66h4M52 66h4"/></svg>
    <h3>Lorem ipsum dolor</h3>
    <p>Praesent porta urna in maximus dapibus. Aliquam velit mi, consectetur ullamcorper quam sit amet, imperdiet</p>
  </div>
  <div class="card" style="left:784px">
    <svg width="76" height="92" viewBox="0 0 76 92" fill="none" stroke="#1b1b1b" stroke-width="3"><rect x="6" y="10" width="64" height="74" rx="12"/><rect x="16" y="20" width="18" height="16" rx="3"/><rect x="42" y="20" width="18" height="16" rx="3"/><rect x="16" y="58" width="18" height="16" rx="3"/><rect x="42" y="58" width="18" height="16" rx="3"/><path d="M30 40h16v14H30z"/></svg>
    <h3>Lorem ipsum dolor</h3>
    <p>Praesent porta urna in maximus dapibus. Aliquam velit mi, consectetur ullamcorper quam sit amet, imperdiet</p>
  </div>
</section>
<div class="abs band"></div>

<h2 class="section-title" style="top:1845px">Our Latest News</h2>
<p class="section-lead" style="top:1914px">Lorem ipsum dolor sit amet, consectetur adipiscing elit. Donec sapien sapien, molestie ac convallis vitae.</p>

<article class="abs news-feature">
  <div class="photo" role="img" aria-label="Photo of a red emergency AED kit beside a person lying on a blue mat"></div>
  <div class="caption">
    <h3>Lorem ipsum dolor sit amet</h3>
    <div class="meta" style="margin-top:14px">
      <svg width="16" height="16" viewBox="0 0 16 16" fill="none" stroke="#fff" stroke-width="1.3"><rect x="1.5" y="3" width="13" height="11.5"/><path d="M1.5 6.5h13M4.5 1v3M11.5 1v3"/></svg>
      12/04/2019<span class="bar"></span>16 min Read . By&nbsp; Rowan
    </div>
  </div>
  <div class="arrows">
    <span><svg width="10" height="12" viewBox="0 0 10 12"><path d="M7 1 2 6l5 5" fill="none" stroke="#17244f" stroke-width="2.4"/></svg></span>
    <span><svg width="10" height="12" viewBox="0 0 10 12"><path d="M3 1l5 5-5 5" fill="none" stroke="#17244f" stroke-width="2.4"/></svg></span>
  </div>
</article>

<div class="abs news-thumb" style="top:2025px;background:linear-gradient(140deg,#c94a3c 0%,#d7d4cc 40%,#5fb0d6 70%,#e3e3e3 100%)" role="img" aria-label="Photo of hands holding AED electrode pads"></div>
<div class="abs news-item" style="top:2039px">
  <div class="meta"><svg width="16" height="16" viewBox="0 0 16 16" fill="none" stroke="#222" stroke-width="1.3"><rect x="1.5" y="3" width="13" height="11.5"/><path d="M1.5 6.5h13M4.5 1v3M11.5 1v3"/></svg>12/04/2019<span class="bar"></span>16 min Read . By&nbsp; Rowan</div>
  <h3>Lorem ipsum dolor sit amet</h3>
  <p>Lorem ipsum dolor sit amet, consectetur adipiscing elit. Donec sapien sapien, molestie ac convallis vitae, gravida ut ex.</p>
  <span class="read-more">Read More</span>
</div>

<div class="abs news-thumb" style="top:2241px;background:linear-gradient(140deg,#8c98a6 0%,#d8d2c6 45%,#7b8a96 75%,#cfd4a0 100%)" role="img" aria-label="Photo of two instructors practising AED use on a training manikin"></div>
<div class="abs news-item" style="top:2252px">
  <div class="meta"><svg width="16" height="16" viewBox="0 0 16 16" fill="none" stroke="#222" stroke-width="1.3"><rect x="1.5" y="3" width="13" height="11.5"/><path d="M1.5 6.5h13M4.5 1v3M11.5 1v3"/></svg>12/04/2019<span class="bar"></span>16 min Read . By&nbsp; Rowan</div>
  <h3>Lorem ipsum dolor sit amet</h3>
  <p>Lorem ipsum dolor sit amet, consectetur adipiscing elit. Donec sapien sapien, molestie ac convallis vitae, gravida ut ex.</p>
  <span class="read-more">Read More</span>
</div>

<section class="abs testimonials">
  <h2>Testimonals</h2>
  <div class="quote-box">
    <span class="qmark" style="top:42px;left:35px">&ldquo;</span>
    <blockquote>Lorem ipsum dolor sit amet, consectetur adipiscing elit. Donec sapien sapien, molestie ac convallis vitae, gravida ut ex. In non sem a velit mollis elementum. Praesent porta urna in maximus dapibus. Aliquam velit mi, consectetur ullamcorper quam sit amet, imperdiet fermentum nunc.</blockquote>
    <span class="qmark" style="top:175px;left:232px">&rdquo;</span>
    <div class="avatar" role="img" aria-label="Client portrait"></div>
    <div class="who"><b>Rowan</b><i>Clients</i></div>
    <div class="case-btn">Read Case Study</div>
  </div>
</section>

<section class="abs map" role="img" aria-label="Greyscale street map of the region with two office locations marked">
  <div class="map-pop" style="left:146px;top:6px;width:210px">72 Fernhollow Rd. Birchfield, BV 11203.<br>(555) 014-0228<br>hello@bv-aed.org</div>
  <svg class="abs" style="left:240px;top:135px" width="24" height="32" viewBox="0 0 24 32"><path d="M12 0a12 12 0 0 0-12 12c0 9 12 20 12 20s12-11 12-20A12 12 0 0 0 12 0z" fill="#e0101c"/><circle cx="12" cy="12" r="5" fill="#fff"/></svg>
  <div class="map-pop" style="left:522px;top:56px;width:212px">410 Larkmoor Avenue, Suite 1902 Birchfield, BV 10418<br>(555) 014-0228<br>hello@bv-aed.org</div>
  <svg class="abs" style="left:625px;top:198px" width="24" height="32" viewBox="0 0 24 32"><path d="M12 0a12 12 0 0 0-12 12c0 9 12 20 12 20s12-11 12-20A12 12 0 0 0 12 0z" fill="#e0101c"/><circle cx="12" cy="12" r="5" fill="#fff"/></svg>
</section>

<footer class="abs footer">
  <div class="brand">
    <div class="brand-seal"></div>
    <div class="brand-name">BIRCHFIELD VALE<br>HEART<br>SOCIETY</div>
  </div>
  <p class="abs" style="top:163px;left:90px;width:285px;font-size:14.5px;line-height:27px;text-align:justify">Lorem ipsum dolor sit amet, consectetur adipiscing elit. Donec sapien sapien, molestie ac convallis vitae, gravida ut ex.</p>
  <h4 style="left:556px">Quick Links</h4>
  <ul style="top:165px;left:556px"><li>Home</li><li>About Us</li><li>Services &amp; Products</li><li>Resources</li><li>Blog</li><li>Contact Us</li></ul>
  <h4 style="left:851px">Contact Us</h4>
  <div class="contact-row" style="top:161px"><svg width="16" height="33" viewBox="0 0 16 33"><path d="M8 10a6 6 0 0 0-6 6c0 4.5 6 10 6 10s6-5.5 6-10a6 6 0 0 0-6-6z" fill="#fff"/><circle cx="8" cy="16" r="2.2" fill="#1b1b1b"/></svg><span>410 Larkmoor Avenue, Suite 1902<br>Birchfield, BV 10418</span></div>
  <div class="contact-row" style="top:227px"><svg width="16" height="33" viewBox="0 0 24 33"><path fill="#fff" d="M6.6 15.8a15 15 0 0 0 6.6 6.6l2.2-2.2c.3-.3.7-.4 1-.2 1.1.4 2.3.6 3.6.6.6 0 1 .4 1 1V25c0 .6-.4 1-1 1A17 17 0 0 1 3 9c0-.6.4-1 1-1h3.5c.6 0 1 .4 1 1 0 1.3.2 2.5.6 3.6.1.3 0 .7-.2 1z"/></svg><span>(555) 014-0228</span></div>
  <div class="contact-row" style="top:260px"><svg width="16" height="33" viewBox="0 0 16 33"><rect x="0" y="11" width="16" height="11" fill="#fff"/><path d="M0 11l8 6 8-6" fill="none" stroke="#1b1b1b" stroke-width="1.4"/></svg><span>hello@bv-aed.org</span></div>
  <div class="copyright">Copyright © 2019 AED. All Rights Reserved</div>
</footer>

</body>
</html>
```